Tour Guide in Israel business card

I am a tour guide in Israel (the holy land). Prior to it I have over 20 years high-tech business. My main (but not only) focus is working with business people that come to Israel and want to get a tour (usually short from few hours to 2 days). During my guiding I incorporate a lot of my know how of the Israeli business culture. I like to have a business card that I can present to anyone that is looking for a tour guide, but that business people will understand the additional value I can provide them during my tour.

Target Market(s)

Business visitors and tourist to Israel

Industry/Entity Type

Tourism

Contact Information for Business Card

Danny Korvath
email: danny@korvath-tours.example
Mobile: +972-52-7416205

Colors

Designer to choose colors to be used in the design.

Requirements
Must have
• Tour Guide
Nice to have
• I don't know how but it should project my understanding in business not just the tourist side of my knowledge.

```html
<!DOCTYPE html>
<html lang="en">
<head>
<meta charset="utf-8">
<title>Danny Korvath – Tour Guide Business Card</title>
<link rel="stylesheet" href="https://fonts.googleapis.com/css2?family=Exo+2:wght@300;400;700&family=Saira+Condensed:wght@300&display=swap">
<style>
  :root {
    --backdrop: #e4e3e1;
    --card-light: #f2f2f2;
    --card-dark: #2a2928;
    --brand-navy: #04344f;
    --ink-grey: #4a4a4a;
    --ink-light: #d8d8d8;
    --ink-soft: #b9c8d3;
    --white: #ffffff;
  }
  html, body {
    margin: 0;
    padding: 0;
    width: 1200px;
    height: 990px;
    overflow: hidden;
    background: var(--backdrop);
  }
  .canvas {
    position: relative;
    width: 1200px;
    height: 990px;
  }
  .card {
    position: absolute;
    top: 366px;
    width: 463px;
    height: 258px;
    overflow: hidden;
  }
  .card--front { left: 118px; background: var(--card-light); }
  .card--back  { left: 619px; background: var(--card-dark); }

  .contact-list {
    position: absolute;
    right: 293px;
    top: 87px;
    margin: 0;
    padding: 0;
    list-style: none;
    text-align: right;
    font-family: "Saira Condensed", sans-serif;
    font-weight: 300;
    font-size: 13px;
    line-height: 21px;
    color: var(--ink-grey);
    text-transform: uppercase;
    white-space: nowrap;
  }
  .name-band {
    position: absolute;
    left: 187px;
    right: 0;
    top: 93px;
    height: 72px;
    background: var(--brand-navy);
    display: flex;
    flex-direction: column;
    align-items: center;
    justify-content: center;
    gap: 5px;
  }
  .name-band__name {
    margin: 0;
    font-family: "Exo 2", sans-serif;
    font-weight: 700;
    font-size: 20px;
    line-height: 22px;
    letter-spacing: 0.5px;
    text-transform: uppercase;
    color: var(--white);
    white-space: nowrap;
  }
  .name-band__role {
    margin: 0;
    font-family: "Exo 2", sans-serif;
    font-weight: 400;
    font-size: 8.5px;
    line-height: 10px;
    letter-spacing: 1.6px;
    text-transform: uppercase;
    color: var(--ink-soft);
    white-space: nowrap;
  }

  .accent-block {
    position: absolute;
    left: 0;
    top: 93px;
    width: 97px;
    height: 72px;
    background: var(--brand-navy);
  }
  .web-address {
    position: absolute;
    left: 97px;
    right: 0;
    top: 93px;
    height: 72px;
    display: flex;
    align-items: center;
    justify-content: center;
    margin: 0;
    font-family: "Exo 2", sans-serif;
    font-weight: 300;
    font-size: 12px;
    letter-spacing: 4.5px;
    text-transform: uppercase;
    color: var(--ink-light);
    white-space: nowrap;
  }
</style>
</head>
<body>
<main class="canvas">
  <section class="card card--front" aria-label="Business card front">
    <ul class="contact-list">
      <li class="contact-list__phone">+972-52-7416205</li>
      <li class="contact-list__email">danny@korvath-tours.example</li>
      <li class="contact-list__web">www.korvath-tours.example</li>
    </ul>
    <div class="name-band">
      <h1 class="name-band__name">Danny Korvath</h1>
      <p class="name-band__role">Tour Guide · Israeli Business Culture</p>
    </div>
  </section>

  <section class="card card--back" aria-label="Business card back">
    <div class="accent-block"></div>
    <p class="web-address">www.korvath-tours.example</p>
  </section>
</main>
</body>
</html>
```